I would like a business card to match my truck wrap and logo. I would like the font to match my existing business card please.

Industry/Entity Type

Painter

Contact Information for Business Card

Rodrigo Fenwar 801-437-2190 Fenwarcoatings.utah@brelmox.com
SERVICES - Custom Paint & Stain, Interior & Exterior, Epoxy Coatings / Garage Floors, Cabinet Refinishing, Log Staining and Refinishing.

Requirements
Nice to have
• I would like to have the white and grey line like the bottom of my vehicle wrap, Light Grey to match my truck also.

```html
<!DOCTYPE html>
<html lang="en">
<head>
<meta charset="utf-8">
<title>Fenwar Coatings – Business Card</title>
<link href="https://fonts.googleapis.com/css2?family=Arimo:wght@400;700&family=Russo+One&display=swap" rel="stylesheet">
<style>
  :root {
    --backdrop: #a9a9a9;
    --blue-bright: #00aaea;
    --blue-deep: #0d5c9b;
    --white: #ffffff;
    --light-grey: #b3b7c3;
    --rule: #6fd0f5;
  }
  * { margin: 0; padding: 0; box-sizing: border-box; }
  html, body { width: 1200px; height: 1200px; overflow: hidden; }
  body {
    background: var(--backdrop);
    position: relative;
    font-family: "Arimo", Arial, sans-serif;
  }
  .card {
    position: absolute;
    top: 304px;
    height: 593px;
    border-radius: 12px;
    overflow: hidden;
    box-shadow: 3px 4px 6px rgba(0,0,0,0.35);
  }
  .card--front {
    left: 200px;
    width: 370px;
    background: linear-gradient(180deg, var(--blue-bright) 0%, #0a84c9 55%, var(--blue-deep) 100%);
    color: var(--white);
  }
  .card--back {
    left: 599px;
    width: 364px;
    background: var(--white);
  }
  .brand {
    position: absolute;
    left: 0; right: 0;
    text-align: center;
    font-family: "Russo One", "Arial Black", sans-serif;
    font-weight: 400;
    line-height: 1;
  }
  .brand__name { display: block; font-size: 50px; letter-spacing: 1px; }
  .brand__tag { display: block; font-size: 20px; letter-spacing: 13px; margin-top: 10px; padding-left: 13px; }
  .card--front .brand { top: 200px; color: var(--white); }
  .card--back .brand { top: 210px; color: var(--blue-bright); }
  .brand-square {
    position: absolute;
    left: 50%;
    width: 64px; height: 64px;
    margin-left: -32px;
    border-radius: 8px;
    transform: rotate(45deg);
  }
  .card--front .brand-square { top: 82px; background: var(--white); }
  .card--back .brand-square { top: 92px; background: var(--blue-bright); }
  .services {
    position: absolute;
    top: 370px;
    left: 0; right: 0;
    text-align: center;
    list-style: none;
    font-size: 19px;
    line-height: 31.3px;
  }
  .services__title { font-weight: 700; font-size: 19px; }
  .stripe-grey {
    position: absolute; left: 0; right: 0;
    top: 352px; height: 8px;
    background: var(--light-grey);
  }
  .contact-panel {
    position: absolute; left: 0; right: 0;
    top: 370px; bottom: 0;
    background: linear-gradient(180deg, var(--blue-bright) 0%, #0a84c9 60%, var(--blue-deep) 100%);
    color: var(--white);
    text-align: center;
    font-family: "Russo One", "Arial Black", sans-serif;
  }
  .contact__name { position: absolute; top: 72px; left: 0; right: 0; font-size: 22px; }
  .contact__rule { position: absolute; top: 106px; left: 120px; width: 125px; height: 1px; background: var(--rule); }
  .contact__phone { position: absolute; top: 118px; left: 0; right: 0; font-size: 22px; }
  .contact__email { position: absolute; top: 146px; left: 0; right: 0; font-size: 16px; }
</style>
</head>
<body>
  <section class="card card--front">
    <div class="brand-square"></div>
    <div class="brand">
      <span class="brand__name">FENWAR</span>
      <span class="brand__tag">COATINGS</span>
    </div>
    <ul class="services">
      <li class="services__title">SERVICES</li>
      <li>Custom Paint &amp; Stain</li>
      <li>Interior &amp; Exterior</li>
      <li>Epoxy Coatings / Garage Floors</li>
      <li>Cabinet Refinishing</li>
      <li>Log Staining and Refinishing.</li>
    </ul>
  </section>

  <section class="card card--back">
    <div class="brand-square"></div>
    <div class="brand">
      <span class="brand__name">FENWAR</span>
      <span class="brand__tag">COATINGS</span>
    </div>
    <div class="stripe-grey"></div>
    <div class="contact-panel">
      <p class="contact__name">RODRIGO FENWAR</p>
      <div class="contact__rule"></div>
      <p class="contact__phone">801-437-2190</p>
      <p class="contact__email">Fenwarcoatings.utah@brelmox.com</p>
    </div>
  </section>
</body>
</html>
```